Figure for presentation on a hybrid research project

We need a figure that shows a series of 6 technical projects feeding into 3 multidisciplinary hybrid projects.
The concept is a ring of 6 technical projects, which could look like a 6 colour swirl (see
https://en.plorvanex.org/wiki/Vector_graphics for an example of a 4 colour swirl.)
The 3 hybrid projects sit in the centre because they rely on input from many of the surrounding technical projects.
I've drawn a rough version in Powerpoint - see attached file uploaded. Note, in my example I couldn't draw the swirling outer ring and the colour selection is poor. The acronym for the overall Centre using the figure is VexORDA, so we will have a mint leaf and turquoise green in the logo, plus also nerves, since we will be researching neural interconnections.
We ABSOLUTELY NEED the final form of the figure to include vector graphics formats (including a form that can be edited in Photoshop) because we may need to change the title of the technical projects or of the hybrid projects at short notice ourselves.

Target Market(s)

Academic: eminent scientists and engineers

Industry/Entity Type

Technical

Font styles to use
Sans Serif

Colors
04a990

Requirements
Must have
• The projects around the ring with all project titles legible; the final figure will be reduced to no more than 8cm x 8cm in the proposal (probably less).
• Only one colour selected, because we have included that colour in the logo that we are having designed. Otherwise, a colour series around the ring that is pleasant, and another compatible colour series for the inter 3 projects.
• We ABSOLUTELY NEED the final form of the figure to include vector graphics formats (including a form that can be edited in Photoshop) because we may need to change the title of the technical projects or of the hybrid projects at short notice ourselves.
Nice to have
• See the figure we uploaded; that's the essence
• HOWEVER VIP: two of the titles around the outer ring have changed slightly.
• Computational Modelling is now Neuronal Modelling and
• Signal Processing is now Non-Invasive Interfaces (note that I've now changed the titles on the uploaded figure)

```html
<!DOCTYPE html>
<html lang="en">
<head>
<meta charset="utf-8">
<title>VexORDA research programme structure</title>
<link rel="stylesheet" href="https://fonts.googleapis.com/css2?family=Lexend:wght@600;700&display=swap">
<style>
  :root {
    --canvas: #ffffff;
    --mint: #05ad94;
    --mint-deep: #037e69;
    --forest: #0b7f63;
    --forest-deep: #04553f;
    --divider: #ffffff;
    --label: #ffffff;
    --hub-wiring: #0399d0;
    --hub-action: #22c5fb;
    --hub-perception: #0130b3;
  }
  html, body {
    margin: 0;
    padding: 0;
    width: 1200px;
    height: 999px;
    overflow: hidden;
    background: var(--canvas);
  }
  .programme-figure {
    display: block;
    width: 1200px;
    height: 999px;
  }
  .petal {
    stroke: var(--divider);
    stroke-width: 5;
    stroke-linejoin: round;
  }
  .petal--light { fill: url(#petal-light); }
  .petal--dark { fill: url(#petal-dark); }
  .label-guide { fill: none; stroke: none; }
  .project-label {
    font-family: "Lexend", "Helvetica Neue", Arial, sans-serif;
    font-weight: 600;
    font-size: 25px;
    fill: var(--label);
    letter-spacing: 0.2px;
  }
  .hub-slice {
    stroke: var(--divider);
    stroke-width: 3;
  }
  .hub-slice--wiring { fill: var(--hub-wiring); }
  .hub-slice--action { fill: var(--hub-action); }
  .hub-slice--perception { fill: var(--hub-perception); }
  .hub-label {
    font-family: "Lexend", "Helvetica Neue", Arial, sans-serif;
    font-weight: 700;
    font-size: 20px;
    fill: var(--label);
    text-anchor: middle;
    dominant-baseline: central;
  }
</style>
</head>
<body>
<svg class="programme-figure" viewBox="0 0 1130 940" role="img" aria-label="Six technical projects in a swirling ring around three hybrid projects">
  <defs>
    <radialGradient id="petal-light" gradientUnits="userSpaceOnUse" cx="560" cy="470" r="365">
      <stop offset="0.45" stop-color="var(--mint-deep)"/>
      <stop offset="1" stop-color="var(--mint)"/>
    </radialGradient>
    <radialGradient id="petal-dark" gradientUnits="userSpaceOnUse" cx="560" cy="470" r="365">
      <stop offset="0.45" stop-color="var(--forest-deep)"/>
      <stop offset="1" stop-color="var(--forest)"/>
    </radialGradient>
    <filter id="hub-shadow" x="-30%" y="-30%" width="160%" height="160%">
      <feDropShadow dx="0" dy="0" stdDeviation="12" flood-color="#013d30" flood-opacity="0.45"/>
    </filter>

    <path id="guide-living" class="label-guide" d="M264.2 321.2 A210 210 0 0 1 629.2 266.6"/>
    <path id="guide-gene" class="label-guide" d="M540.9 139.4 A210 210 0 0 1 770.7 428.2"/>
    <path id="guide-electro" class="label-guide" d="M701.5 631.6 A210 210 0 0 0 836.8 288.2"/>
    <path id="guide-optrode" class="label-guide" d="M490.8 673.4 A210 210 0 0 0 855.8 618.8"/>
    <path id="guide-neuronal" class="label-guide" d="M349.3 511.8 A210 210 0 0 0 579.1 800.6"/>
    <path id="guide-noninvasive" class="label-guide" d="M283.2 651.8 A210 210 0 0 1 418.5 308.4"/>
  </defs>

  <g class="technical-ring">
    <path class="petal petal--dark" d="M223.4 422.7 A240 240 0 1 1 682.3 487.2 A240 240 0 0 0 223.4 422.7 Z"/>
    <path class="petal petal--light" d="M432.7 154.8 A240 240 0 1 1 606.2 584.5 A240 240 0 0 0 432.7 154.8 Z"/>
    <path class="petal petal--dark" d="M769.3 202.1 A240 240 0 1 1 484.0 567.3 A240 240 0 0 0 769.3 202.1 Z"/>
    <path class="petal petal--light" d="M896.6 517.3 A240 240 0 1 1 437.7 452.8 A240 240 0 0 0 896.6 517.3 Z"/>
    <path class="petal petal--dark" d="M687.3 785.2 A240 240 0 1 1 513.8 355.5 A240 240 0 0 0 687.3 785.2 Z"/>
    <path class="petal petal--light" d="M350.7 737.9 A240 240 0 1 1 636.0 372.7 A240 240 0 0 0 350.7 737.9 Z"/>
  </g>

  <g class="technical-labels">
    <text class="project-label"><textPath href="#guide-living" startOffset="50%" text-anchor="middle" dominant-baseline="central">Living Electrodes</textPath></text>
    <text class="project-label"><textPath href="#guide-gene" startOffset="50%" text-anchor="middle" dominant-baseline="central">Gene Regulated Interfaces</textPath></text>
    <text class="project-label"><textPath href="#guide-electro" startOffset="50%" text-anchor="middle" dominant-baseline="central">Electro-modulated Interfaces</textPath></text>
    <text class="project-label"><textPath href="#guide-optrode" startOffset="50%" text-anchor="middle" dominant-baseline="central">Optrode Interfaces</textPath></text>
    <text class="project-label"><textPath href="#guide-neuronal" startOffset="50%" text-anchor="middle" dominant-baseline="central">Neuronal Modeling</textPath></text>
    <text class="project-label"><textPath href="#guide-noninvasive" startOffset="50%" text-anchor="middle" dominant-baseline="central">Non-invasive Interfaces</textPath></text>
  </g>

  <g class="hybrid-hub" filter="url(#hub-shadow)">
    <path class="hub-slice hub-slice--wiring" d="M560 470 L404.1 380 A180 180 0 0 1 715.9 380 Z"/>
    <path class="hub-slice hub-slice--perception" d="M560 470 L715.9 380 A180 180 0 0 1 560 650 Z"/>
    <path class="hub-slice hub-slice--action" d="M560 470 L560 650 A180 180 0 0 1 404.1 380 Z"/>
  </g>
  <g class="hybrid-labels">
    <text class="hub-label" x="560" y="374">BRAIN WIRING</text>
    <text class="hub-label" x="473" y="512">ACTION</text>
    <text class="hub-label" x="646" y="512">PERCEPTION</text>
  </g>
</svg>
</body>
</html>
```